Powerpoint design template for LUMOTEX for new digital platform

We would like to use a PowerPoint template, we would like to create a new page, we would like to create a new digital platform LUMOTEX for schools and parents for the creation of playful communication and educational tools for children to enhance their positive development, amaze them learn in a playful way. This platform is going to be the most creative, stimulating and innovative classroom, easy to use and fast to implement. Scrapbooking, collages ... Magazine, newsletters Diplomla / awards Slideshows Facebook Calendars Organizers Greetings Games ... This powerpoint template will be used essential to We are looking for a professional design, positioning our brand in the children market with an adult hearing. so you will need to find a good deal. Primary target: nurseries & schools from 0 to 18 years old and universities (in 2nd phase) Secondary target: small & medium businesses Third target: general public, and TPE If it is a color scheme, then it is suggested that it be marketed in Europe (UK, Italy, Spain) and in a 2nd Stage USA and other countries. multiple options for front page, insidious pages (multiple styles with limited text and extended text) and final contact page We need something to read, we can not do it too much, but we can not do it. , and inside pages aligned to our logo

Target Market(s)

Target 1; Education with teacher Target 2; parents and grandparents

Industry/Entity Type

Education

Font styles to use
Other font styles liked:
• not decided. but not too fancy

Requirements
Must have
• Multi page options for front page, page insides (multiple styles with limited text and extended text) and final page contact
Nice to have
• do not have a lot of ideas. We need something to read, we can not get away from it
Should not have
• not too fancy and busy: keep clarity & simplicity while reassuring on quality

```html
<!DOCTYPE html>
<html lang="en">
<head>
<meta charset="utf-8">
<title>LUMOTEX – Project Slide</title>
<link href="https://fonts.googleapis.com/css2?family=Roboto+Condensed:wght@400;700&family=Mulish:wght@400;600&display=swap" rel="stylesheet">
<style>
  :root {
    --lime: #d9e042;
    --leaf: #b4cc38;
    --green: #8cc63e;
    --orange: #f7941d;
    --ink: #2b2b2b;
    --body: #4a4a4a;
    --gold: #f9b52c;
    --pink: #e8317a;
    --purple: #9479b3;
    --white: #ffffff;
  }
  * { margin: 0; padding: 0; box-sizing: border-box; }
  html, body { width: 1200px; height: 900px; overflow: hidden; background: var(--white); }
  .slide { position: relative; width: 1200px; height: 900px; overflow: hidden; background: var(--white); }
  .band { position: absolute; left: 0; }
  .band--top { top: 0; }
  .band--bottom { bottom: 0; }
  .slide-title {
    position: absolute; left: 30px; top: 30px;
    font: 700 44px/1 "Roboto Condensed", sans-serif;
    color: var(--ink); letter-spacing: 0.2px;
  }
  .brand { position: absolute; left: 995px; top: 40px; display: flex; flex-direction: column; }
  .brand-name { font: 600 40px/1 "Mulish", sans-serif; color: var(--pink); letter-spacing: 1px; }
  .brand-tagline { margin-top: 8px; font: 600 8px/1.3 "Mulish", sans-serif; color: var(--ink); letter-spacing: 1.5px; width: 90px; }
  .points { position: absolute; left: 0; top: 0; width: 100%; }
  .point { position: absolute; left: 57px; display: flex; }
  .point-icon { width: 62px; height: 68px; background: var(--purple); border-radius: 4px; transform: rotate(-18deg); margin-top: 2px; }
  .point-text { position: absolute; left: 115px; top: 0; width: 960px; }
  .point-heading { font: 600 30px/1.1 "Mulish", sans-serif; }
  .point-heading--gold { color: var(--gold); }
  .point-heading--pink { color: var(--pink); }
  .point-body { font: 400 25px/36px "Mulish", sans-serif; color: var(--body); margin-top: 4px; }
  .footer-url { position: absolute; left: 21px; bottom: 20px; font: 400 25px/1 "Roboto Condensed", sans-serif; color: var(--ink); }
  .page-number { position: absolute; right: 36px; bottom: 20px; font: 400 25px/1 "Roboto Condensed", sans-serif; color: var(--ink); }
</style>
</head>
<body>
<main class="slide">
  <svg class="band band--top" width="1200" height="120" viewBox="0 0 1200 120" aria-hidden="true">
    <polygon points="930,0 990,0 945,105 900,110" fill="var(--green)"/>
    <polygon points="915,0 975,0 925,90 905,110" fill="var(--leaf)"/>
    <polygon points="0,0 955,0 900,110 0,110" fill="var(--lime)"/>
  </svg>
  <h1 class="slide-title">PROJECT TITLE HERE</h1>
  <div class="brand">
    <span class="brand-name">LUMOTEX</span>
    <span class="brand-tagline">YOUR TAGLINE GOES HERE</span>
  </div>

  <section class="points">
    <article class="point" style="top:277px">
      <div class="point-icon" role="img" aria-label="Purple book icon"></div>
      <div class="point-text">
        <h2 class="point-heading point-heading--gold">Subtext here</h2>
        <p class="point-body">Lemon drops oat cake oat cake sugar plum sweet gingerbread chocolate cake gingerbread. Lemon drops oat cake oat cake sugar plum sweet</p>
      </div>
    </article>
    <article class="point" style="top:440px">
      <div class="point-icon" role="img" aria-label="Purple book icon"></div>
      <div class="point-text">
        <h2 class="point-heading point-heading--pink">Subtext here</h2>
        <p class="point-body">Lemon drops oat cake oat cake sugar plum sweet gingerbread chocolate cake gingerbread. Lemon drops oat cake oat cake sugar plum sweet</p>
      </div>
    </article>
    <article class="point" style="top:619px">
      <div class="point-icon" role="img" aria-label="Purple book icon"></div>
      <div class="point-text">
        <h2 class="point-heading point-heading--pink">Subtext here</h2>
        <p class="point-body">Lemon drops oat cake oat cake sugar plum sweet gingerbread chocolate cake gingerbread. Lemon drops oat cake oat cake sugar plum sweet</p>
      </div>
    </article>
  </section>

  <svg class="band band--bottom" width="1200" height="70" viewBox="0 0 1200 70" aria-hidden="true">
    <polygon points="0,4 975,4 1035,70 0,70" fill="var(--lime)"/>
    <polygon points="975,4 990,4 1050,70 1035,70" fill="var(--leaf)"/>
    <polygon points="980,0 995,0 1062,70 1045,70" fill="var(--green)"/>
    <polygon points="997,4 1200,4 1200,70 1058,70" fill="var(--orange)"/>
  </svg>
  <span class="footer-url">www.lumotex.com</span>
  <span class="page-number">Page : 01</span>
</main>
</body>
</html>
```